Satchel & Sundial needs new business card design

I need a new business card design. I'm looking for out-of-the-box design which represents the freedom of being a location independent entrepreneur.
I offer coaching, retreats and trips.
I would like to see designs with and without the photo.
Colors I use are black (#000000), green (#25A796) and brown (#D7C38C)
Website satchelandsundial.example

Target Market(s)

location independent entrepreneurs, digital nomads, people looking to swap the 9 to 5 for a lifestyle business

Industry/Entity Type

Business

Contact Information for Business Card

Dorota Falkner
Your Lifestyle Business Coach, Retreat & Trip Leader
http://satchelandsundial.example
hello@satchelandsundial.example
Live a life you don't need a holiday from

Font styles to use
Serif
Sans Serif

Requirements
Must have
• One side should contain only the logo. I would also consider having the "Live a life you don't need a holiday from" on that side too (depending on how it looks)
• Please show both sides on the designs.

```html
<!DOCTYPE html>
<html lang="en">
<head>
<meta charset="utf-8">
<title>Satchel &amp; Sundial — Business Card</title>
<link rel="stylesheet" href="https://fonts.googleapis.com/css2?family=Roboto:wght@400;500;700&display=swap">
<style>
  :root {
    --teal: #25a796;
    --teal-deep: #1c8f80;
    --ink: #000000;
    --charcoal: #1c1c1d;
    --text-grey: #3a3a3a;
    --paper: #ffffff;
    --backdrop: #3b3c3e;
    --edge-grey: #dcdcdc;
  }
  * { box-sizing: border-box; margin: 0; padding: 0; }
  html, body {
    width: 1200px; height: 843px; overflow: hidden;
    background: var(--backdrop);
    font-family: "Roboto", Arial, sans-serif;
  }
  .stage {
    width: 1200px; height: 843px;
    display: flex; flex-direction: column;
    align-items: center; justify-content: center; gap: 40px;
  }
  .card {
    position: relative;
    width: 660px; height: 377px;
    overflow: hidden;
    border-radius: 3px;
  }
  /* Back side: logo only */
  .card--back {
    background: linear-gradient(160deg, #2eb3a1 0%, var(--teal) 45%, var(--teal-deep) 100%);
    display: flex; align-items: center; justify-content: center;
  }
  .card--back .brand-name {
    color: var(--paper);
    font-weight: 700;
    font-size: 50px;
    letter-spacing: 3px;
    text-transform: uppercase;
  }
  /* Front side */
  .card--front { background: var(--charcoal); }
  .card-shape { position: absolute; inset: 0; width: 100%; height: 100%; }
  .front-content {
    position: absolute; left: 46px; top: 34px; width: 500px;
  }
  .front-content .brand-name {
    color: var(--ink);
    font-weight: 700;
    font-size: 34px;
    letter-spacing: 2px;
    text-transform: uppercase;
    margin-bottom: 42px;
    margin-left: 34px;
  }
  .person-name {
    color: var(--teal);
    font-weight: 500;
    font-size: 22px;
    margin-bottom: 4px;
  }
  .person-role {
    color: var(--text-grey);
    font-size: 18px;
    line-height: 1.25;
    margin-bottom: 18px;
  }
  .contact-list { list-style: none; }
  .contact-item {
    display: flex; align-items: center; gap: 10px;
    color: var(--text-grey);
    font-size: 16px;
    line-height: 1.45;
  }
  .contact-icon { width: 16px; height: 16px; flex: none; }
  .tagline {
    position: absolute;
    left: 636px; top: 188px;
    transform: translate(-50%, -50%) rotate(-90deg);
    white-space: nowrap;
    color: var(--paper);
    font-size: 14px;
    letter-spacing: 0.3px;
  }
</style>
</head>
<body>
<main class="stage">

  <section class="card card--back" aria-label="Card back">
    <p class="brand-name">Satchel &amp; Sundial</p>
  </section>

  <section class="card card--front" aria-label="Card front">
    <svg class="card-shape" viewBox="0 0 660 377" aria-hidden="true">
      <path d="M0 0 H540 C604 60 620 222 578 302 C548 352 486 377 424 377 H0 Z" fill="var(--teal)"/>
      <path d="M0 0 H540 C602 60 610 210 566 290 C530 348 450 377 370 377 H0 Z" fill="var(--edge-grey)"/>
      <path d="M0 0 H536 C598 60 604 208 558 286 C520 346 440 377 356 377 H0 Z" fill="var(--paper)"/>
    </svg>

    <div class="front-content">
      <p class="brand-name">Satchel &amp; Sundial</p>
      <h1 class="person-name">Dorota Falkner</h1>
      <p class="person-role">Your Lifestyle Business Coach<br>Retreat &amp; Trip Leader</p>
      <ul class="contact-list">
        <li class="contact-item">
          <svg class="contact-icon" viewBox="0 0 16 16" aria-hidden="true">
            <rect x="1" y="3" width="14" height="10" rx="1.5" fill="var(--teal)"/>
            <path d="M1.5 4 L8 9 L14.5 4" fill="none" stroke="var(--paper)" stroke-width="1.3"/>
          </svg>
          hello@satchelandsundial.example
        </li>
        <li class="contact-item">
          <svg class="contact-icon" viewBox="0 0 16 16" aria-hidden="true">
            <circle cx="8" cy="8" r="7" fill="var(--teal)"/>
            <ellipse cx="8" cy="8" rx="3" ry="6.5" fill="none" stroke="var(--paper)" stroke-width="1"/>
            <line x1="1.5" y1="8" x2="14.5" y2="8" stroke="var(--paper)" stroke-width="1"/>
          </svg>
          www.satchelandsundial.example
        </li>
      </ul>
    </div>

    <p class="tagline">Live a life you don't need a holiday from</p>
  </section>

</main>
</body>
</html>
```